Environmental Consultancey needs Web Design

A consultancey firm based in Papua New Guinea specialising servicing a client market primarily in Melanesia, the wider Pacific Region and South East Asia. The firm provides services to community development and resource extraction activites that incorporate sustainable livelihoods for local customary land owners with environmentally responsibile practices and a focus on maintaining biodiversity and ecosystem services. We aim to encompass Culture, Custom and Science in our approach. Our website preferentially will convey a relaxed Pacific Island feel in its colours and design rather than a sterile corporate feel. See attached logo that will need to be visible on page or which may provide basis for ideas for the page.

Target Market(s)

Our target market is primarily the oil, gas and mining industry, secondarily international donor and aid programs followed by government projects and not for profit programs. Services include:
1. Biodiversity and Conservation - Fauna and Flora survey, assessment, management, monitoring & research, protected areas & endangered & threatend species.
2. Social & Community - impact, stakeholder engagement, census and survey, land and community affairs, capacity building empowerment.
3. Environmental Management - sustainable use, enterprise development & management, biodiversity offsets.

Industry/Entity Type

Community

Requirements
Must have
• Multiple pages, Logo somewhere on home page. Space for a couple of photos that as yet ive not decieded upon.
Nice to have
• Perhaps incorporate shapes, texture and colours that convey a feel of the attached photo of a blue bird of paradise. The blue fine overlapping and interlocking feather patterns are appealing perhaps as a background and the other colours used in boarders ? Abstract is fine as would be symbolic images or tribal ambience. The company is all about blending humanity in all its forms with the environment.

```html
<!DOCTYPE html>
<html lang="en">
<head>
<meta charset="utf-8">
<title>Verdant Reef Partners</title>
<link rel="stylesheet" href="https://fonts.googleapis.com/css2?family=Roboto+Condensed:wght@400;700&family=Chewy&display=swap">
<style>
:root{
  --leaf:#9cc42b;
  --leaf-dark:#7fa81c;
  --sun-top:#fde85a;
  --sun-bottom:#f5cf2c;
  --lagoon:#009b97;
  --lagoon-soft:#0aa9a4;
  --plume:#1b5fc0;
  --heading-teal:#13999a;
  --heading-blue:#2464b4;
  --ink:#111;
  --panel:#ffffff;
  --panel-edge:#e3e3e3;
  --alert:#e8262b;
  --wood:#7a5432;
}
*{box-sizing:border-box;margin:0;padding:0}
html,body{width:1057px;height:1200px;overflow:hidden}
body{
  position:relative;
  background:radial-gradient(circle at 50% 40%,#a6cc33 0%,var(--leaf) 55%,var(--leaf-dark) 100%);
  font-family:"Roboto Condensed",Arial,sans-serif;
  color:var(--ink);
}
.main-nav{
  position:absolute;left:12px;top:79px;width:1033px;height:47px;
  background:linear-gradient(var(--sun-top),var(--sun-bottom));
  border-radius:4px 4px 0 0;
}
.main-nav a{
  position:absolute;top:16px;font-size:14px;color:var(--ink);text-decoration:none;
}
.brand-badge{
  position:absolute;left:400px;top:8px;width:186px;height:186px;border-radius:50%;
  background:#fff;border:3px solid #e9e9e9;z-index:2;
  display:flex;align-items:center;justify-content:center;text-align:center;
  font-size:22px;font-weight:700;color:var(--heading-teal);line-height:1.15;
}
.hero{position:absolute;left:12px;top:126px;width:1033px;height:359px}
.hero-photo{
  position:absolute;left:0;top:0;width:474px;height:359px;
  background:linear-gradient(135deg,#8a7050 0%,#2f6fd6 45%,#1b3f9a 70%,#c9b99a 100%);
}
.hero-panel{position:absolute;left:474px;top:0;width:559px;height:359px;background:var(--lagoon)}
.hero-tree{
  position:absolute;left:144px;top:36px;width:196px;height:216px;
  background:var(--lagoon-soft);border-radius:50% 50% 8px 8px;
}
.hero-title{
  position:absolute;left:45px;top:244px;color:#fff;text-transform:uppercase;
  font-size:31px;line-height:44px;text-shadow:1px 1px 2px rgba(0,0,0,.25);
}
.hero-title .big{font-size:39px}
.panel{
  position:absolute;left:11px;width:1037px;background:linear-gradient(#fff 60%,#f0f0f0);
  border:1px solid var(--panel-edge);border-radius:4px;
}
.spotlight{top:491px;height:185px}
.projects{top:686px;height:364px}
.panel h2{font-weight:400;font-size:18px;color:var(--heading-teal);position:absolute}
.spot{position:absolute;top:28px;width:215px}
.spot h2{position:static;margin-bottom:14px}
.spot p{font-size:12px;line-height:15px}
.more-btn{
  display:block;margin-top:14px;margin-left:4px;width:94px;height:26px;border:1px solid #d6d6d6;
  border-radius:3px;background:#fff;font-size:12px;line-height:24px;padding-left:12px;color:#2b4b4b;
}
.join h2{position:static;margin-bottom:12px}
.field{position:absolute;width:142px;height:29px;border:1px solid #cfcfcf;border-radius:4px;background:#fff}
.sign-in{
  position:absolute;left:955px;top:103px;width:55px;height:24px;border-radius:3px;
  background:var(--alert);color:#fff;font-size:12px;line-height:24px;padding-left:9px;
}
.projects .title{left:24px;top:28px;color:var(--heading-blue)}
.project{position:absolute;top:68px;width:290px}
.project-frame{width:219px;height:124px;border:1px solid #ddd;background:#fff;padding:7px}
.project-photo{width:100%;height:100%}
.project h3{font-weight:400;font-size:12px;color:var(--heading-teal);margin:14px 0 15px;text-transform:uppercase}
.project p{font-size:12px;line-height:15px}
.social{position:absolute;top:1063px;text-align:center;font-family:"Chewy","Roboto Condensed",sans-serif;font-size:21px}
.social .dot{width:60px;height:60px;border-radius:50%;background:var(--wood);margin:0 auto 8px;border:3px solid #a07a4c}
.foot-mark{
  position:absolute;left:874px;top:1062px;width:60px;height:60px;border-radius:50%;background:#fff;
  font-size:10px;font-weight:700;color:var(--heading-teal);display:flex;align-items:center;justify-content:center;text-align:center;line-height:1.1;
}
.copyright{position:absolute;right:30px;top:1130px;color:#fff;font-weight:700;font-size:16px}
</style>
</head>
<body>
<nav class="main-nav">
  <a style="left:40px">Home</a><a style="left:113px">Donate</a><a style="left:196px">Join Us</a><a style="left:280px">Take Action</a>
  <a style="left:596px">Volunteer</a><a style="left:691px">What We Do</a><a style="left:801px">Blogs/Media</a><a style="left:913px">Photos/Video</a>
</nav>
<div class="brand-badge">Verdant Reef<br>Partners</div>

<section class="hero">
  <div class="hero-photo" role="img" aria-label="Photo of a blue bird of paradise on a branch"></div>
  <div class="hero-panel">
    <div class="hero-tree" role="img" aria-label="Line drawing of a tree"></div>
    <h1 class="hero-title">Encompassing <span class="big">Culture,</span><br><span class="big">Custom &amp; Science</span></h1>
  </div>
</section>

<section class="panel spotlight">
  <div class="spot" style="left:24px"><h2>In the spotlight:</h2><p>These are the five words that say a lot but apparently mean little to a company that has made a mantra out of repeating something which is simply not true.</p><span class="more-btn">find out more</span></div>
  <div class="spot" style="left:282px"><h2>In the spotlight:</h2><p>These are the five words that say a lot but apparently mean little to a company that has made a mantra out of repeating something which is simply not true.</p><span class="more-btn">find out more</span></div>
  <div class="spot" style="left:550px"><h2>In the spotlight:</h2><p>These are the five words that say a lot but apparently mean little to a company that has made a mantra out of repeating something which is simply not true.</p><span class="more-btn">find out more</span></div>
  <div class="spot join" style="left:806px"><h2>Join Us</h2></div>
  <div class="field" style="left:808px;top:59px"></div>
  <div class="field" style="left:808px;top:98px"></div>
  <span class="sign-in">sign in</span>
</section>

<section class="panel projects">
  <h2 class="title">Our projects!</h2>
  <div class="project" style="left:25px"><div class="project-frame"><div class="project-photo" role="img" aria-label="Close photo of a blue bird of paradise" style="background:linear-gradient(135deg,#1f3f8c,#4c8fe0 60%,#a9d5f0)"></div></div><h3>Encompassing culture, custom &amp; science</h3><p>These are the five words that say a lot but apparently mean little to a company that has made a mantra out of repeating something which is simply not true.</p></div>
  <div class="project" style="left:366px"><div class="project-frame"><div class="project-photo" role="img" aria-label="Photo of orange reef fish over coral" style="background:linear-gradient(160deg,#1f5fb0,#e36a3a 55%,#2a4f8c)"></div></div><h3>Encompassing culture, custom &amp; science</h3><p>These are the five words that say a lot but apparently mean little to a company that has made a mantra out of repeating something which is simply not true.</p></div>
  <div class="project" style="left:717px"><div class="project-frame"><div class="project-photo" role="img" aria-label="Photo of a dolphin in blue water" style="background:linear-gradient(135deg,#2aa0d8,#7e8c96 55%,#1a84c6)"></div></div><h3>Encompassing culture, custom &amp; science</h3><p>These are the five words that say a lot but apparently mean little to a company that has made a mantra out of repeating something which is simply not true.</p></div>
</section>

<div class="social" style="left:40px"><div class="dot"></div>join us on Kinnet</div>
<div class="social" style="left:258px"><div class="dot"></div>post about us</div>
<div class="foot-mark">Verdant Reef<br>Partners</div>
<div class="copyright">Verdant Reef Partners ©2012 |</div>
</body>
</html>
```